Garlic Farm for Farm Sales/Restaurant sales

Need a professional, but appealing to agriculture world. We are selling 27 kinds of Organic Garlic from a farm in Simla,CO. I have uploaded logo and business information-we are going to need a template, because I will need to use it for four separate people.
-We are trying to appeal to Farm to table restaurants
-As well as growers/farmers

Target Market(s)

Agriculture Sales/Restaurants-Organic

Industry/Entity Type

Agriculture

Contact Information for Business Card

Want it to look more unique then your average kelto stock card- I want it to look amazing

Font styles to use
Sans Serif

Colors
0455a3
ec1f27
fbed22
ffffff

Requirements
Must have
• Just be creative
Nice to have
• Colorful
Should not have
• plain

```html
<!DOCTYPE html>
<html lang="en">
<head>
<meta charset="utf-8">
<title>Summit Ridge Garlic – Business Card</title>
<link rel="stylesheet" href="https://fonts.googleapis.com/css2?family=Source+Sans+3:wght@400;600;700&display=swap">
<style>
  :root {
    --stage: #000000;
    --card-white: #ffffff;
    --card-yellow: #fdd800;
    --brand-navy: #0e2c6b;
    --brand-red: #c8102e;
    --logo-red: #d62230;
    --ink: #1a1a1a;
    --faint-orange: rgba(240, 150, 20, 0.35);
  }
  * { margin: 0; padding: 0; box-sizing: border-box; }
  html, body {
    width: 1200px; height: 900px; overflow: hidden;
    background: var(--stage);
    font-family: "Source Sans 3", Arial, sans-serif;
  }
  .stage { position: relative; width: 1200px; height: 900px; }

  .card { position: absolute; top: 275px; width: 477px; height: 294px; overflow: hidden; }
  .card--front {
    left: 116px; background: var(--card-white);
    border-radius: 0 46px 0 46px;
  }
  .card--back {
    left: 622px; top: 276px; height: 293px; background: var(--card-yellow);
    border-radius: 46px 0 46px 0;
  }

  /* brand lockup */
  .brand { position: absolute; display: flex; flex-direction: column; align-items: center; }
  .brand__mark { border-radius: 50%; }
  .brand__name {
    font-weight: 700; color: var(--brand-navy); white-space: nowrap; line-height: 1;
  }
  .card--front .brand { left: 30px; top: 46px; width: 222px; }
  .card--front .brand__mark { width: 92px; height: 92px; background: var(--logo-red); margin-bottom: 14px; }
  .card--front .brand__name { font-size: 30px; }

  .card--back .brand { left: 0; right: 0; top: 14px; }
  .card--back .brand__mark { width: 262px; height: 262px; background: var(--faint-orange); }
  .card--back .brand__name {
    position: absolute; top: 196px; font-size: 40px;
  }

  /* person + contact */
  .person { position: absolute; right: 19px; top: 35px; text-align: right; }
  .person__name { font-size: 20px; font-weight: 700; color: var(--brand-red); line-height: 1.1; }
  .person__role { font-size: 13.5px; color: var(--ink); margin-top: 3px; }

  .address {
    position: absolute; right: 21px; top: 157px; text-align: right;
    font-size: 13.5px; line-height: 17px; color: var(--ink); font-style: normal;
  }

  .contact { position: absolute; right: 20px; top: 216px; list-style: none; }
  .contact__item {
    display: flex; justify-content: flex-end; align-items: center; gap: 7px;
    font-size: 13.5px; line-height: 17.5px; color: var(--ink);
  }
  .contact__icon { width: 10px; height: 10px; fill: var(--brand-red); flex: none; }
</style>
</head>
<body>
<main class="stage">

  <section class="card card--front" aria-label="Business card front">
    <div class="brand">
      <div class="brand__mark"></div>
      <span class="brand__name">Summit Ridge Garlic</span>
    </div>

    <header class="person">
      <h1 class="person__name">Daniel Reyes</h1>
      <p class="person__role">Managing Director</p>
    </header>

    <address class="address">
      4820, Prairie Field Road<br>
      Eastfield, 804210
    </address>

    <ul class="contact">
      <li class="contact__item">055-987 654 321
        <svg class="contact__icon" viewBox="0 0 10 10" aria-hidden="true"><path d="M2 0.5 L3.6 2.6 L2.8 3.8 C3.5 5.3 4.7 6.5 6.2 7.2 L7.4 6.4 L9.5 8 L8.6 9.5 C4.5 9.2 0.8 5.5 0.5 1.4 Z"/></svg>
      </li>
      <li class="contact__item">hello@summitridge.com
        <svg class="contact__icon" viewBox="0 0 10 10" aria-hidden="true"><path d="M0.5 2 H9.5 V8 H0.5 Z M0.5 2 L5 5.3 L9.5 2" /><path d="M1 2.4 L5 5.2 L9 2.4" stroke="#fff" stroke-width="0.9" fill="none"/></svg>
      </li>
      <li class="contact__item">www.summitridgefarm.com
        <svg class="contact__icon" viewBox="0 0 10 10" aria-hidden="true"><path d="M4 6 L6 4 M3.2 5 L1.6 6.6 A1.4 1.4 0 0 0 3.4 8.4 L5 6.8 M5 3.2 L6.6 1.6 A1.4 1.4 0 0 1 8.4 3.4 L6.8 5" stroke="#c8102e" stroke-width="1.2" fill="none" stroke-linecap="round"/></svg>
      </li>
    </ul>
  </section>

  <section class="card card--back" aria-label="Business card back">
    <div class="brand">
      <div class="brand__mark"></div>
      <span class="brand__name">Summit Ridge Garlic</span>
    </div>
  </section>

</main>
</body>
</html>
```